New website design and logo for FlintBoro.com to help ignite the website sales.

Hi designers,

Flintboro is a new welding brand that is selling welding equipement.

Currently I have around 5 to 10 products. The issue is that the site itself does not do that much of sales. So I have to do something about the seo etc. but that is out of scope for the design.

What is in scope is to comeup with a new logo and website look and feel that is in line with the customers.

men, non professionals, garage, home improvements, perhaps sme ( small mediul entreprice business that want to start in the welding industry.

Products are midrange prices and quality. The look and feel must breath cool stuff, sexy ( women in working cloths carrying welding gloves, other protection gear and weldels)

The wedsite is build in wordpress with the Kora theme. I am an IT guy myself withhout any creativity in me :( so if you can help me with that that would be great.

Please have a quick look at flintboro.com

Best regards,
Joris

Target Market(s)

non professional welders that do metal work in there garage

Coding

Coded - Design and coding required

Number of Pages Required

3 page

Font styles to use
Sans Serif

Colors
0355a3
ffc214

Requirements
Must have
• I would like to see a new homepage and product page design together with a new logo.
Nice to have
• shop design

```html
<!DOCTYPE html>
<html lang="en">
<head>
<meta charset="utf-8">
<title>FlintBoro – Welding Equipment</title>
<link href="https://fonts.googleapis.com/css2?family=Roboto:wght@400;500;700&family=Tinos:ital@0;1&display=swap" rel="stylesheet">
<style>
:root{
  --blue:#0355a3;
  --blue-bright:#1a5fc4;
  --gold:#ffc214;
  --orange:#f7a11a;
  --ink:#111;
  --text:#555;
  --pale:#eaf2fa;
  --footer:#111;
}
*{box-sizing:border-box;margin:0;padding:0}
html,body{width:1200px;height:3543px;overflow:hidden}
body{font-family:"Roboto",sans-serif;color:var(--ink);background:#fff;position:relative}
.serif{font-family:"Tinos",serif}
.abs{position:absolute}

/* top bar */
.topbar{position:absolute;left:0;top:0;width:1200px;height:43px;background:var(--blue-bright);color:#fff;font:15px "Tinos",serif;display:flex;align-items:center;justify-content:center;gap:6px}

/* header */
.header{position:absolute;left:0;top:43px;width:1200px;height:107px;background:#fff}
.brand{position:absolute;left:121px;top:10px;display:flex;align-items:center;gap:8px;font:700 22px "Roboto",sans-serif;color:var(--blue)}
.brand .mark{width:30px;height:30px;background:var(--orange);border-radius:50%}
.search{position:absolute;left:489px;top:11px;width:402px;height:43px;border:1px solid #ccc;display:flex}
.search span{flex:1;padding:0 14px;font-size:13px;color:#999;line-height:41px}
.search .btn{width:48px;background:var(--orange);display:flex;align-items:center;justify-content:center}
.call{position:absolute;left:900px;top:10px;display:flex;gap:8px;align-items:center}
.call .lbl{font:15px "Tinos",serif;color:#333;line-height:17px}
.call .num{font:500 17px "Roboto",sans-serif;color:var(--blue-bright)}
.nav{position:absolute;top:73px;left:0;width:1200px;font:500 16px "Roboto",sans-serif}
.nav a{position:absolute;color:#111;text-decoration:none;white-space:nowrap}
.nav a.active{color:var(--orange)}
.acct{position:absolute;top:72px;font:16px "Tinos",serif;color:#222;display:flex;align-items:center;gap:5px}
.cart{position:absolute;left:1025px;top:71px;width:63px;height:28px;border:1px solid #ccc;font:15px "Tinos",serif;color:#555;display:flex;align-items:center;justify-content:center;gap:6px}
.cart .badge{position:absolute;left:-22px;top:-8px;width:18px;height:18px;border-radius:50%;background:var(--blue-bright);color:#fff;font:700 11px "Roboto";display:flex;align-items:center;justify-content:center}

/* hero */
.hero{position:absolute;left:0;top:150px;width:1200px;height:515px;background:linear-gradient(100deg,#101a26 0%,#1d2f44 45%,#3a4c62 70%,#203a5c 100%)}
.hero h1{position:absolute;left:111px;top:145px;width:520px;font:700 37px/48px "Roboto",sans-serif;color:#fff}
.btn-gold{display:flex;align-items:center;justify-content:center;background:var(--orange);color:#fff;font:500 17px "Roboto",sans-serif;text-transform:uppercase}
.hero .btn-gold{position:absolute;left:111px;top:308px;width:170px;height:46px}
.dots{position:absolute;left:52px;top:216px;display:flex;flex-direction:column;gap:13px}
.dots i{width:12px;height:12px;border-radius:50%;background:#8a8f96;display:block}
.dots i.on{background:#fff}

/* welcome */
.welcome-frame{position:absolute;left:132px;top:747px;width:421px;height:395px;border:2px solid var(--orange);border-radius:8px}
.welcome-img{position:absolute;left:149px;top:764px;width:422px;height:395px;border-radius:8px;background:radial-gradient(circle at 45% 55%,#c9d6e6 0%,#5b7495 22%,#3a3f4a 55%,#4a3a36 100%)}
.eyebrow{font:26px "Tinos",serif;color:var(--blue-bright)}
.h2{font:700 40px "Roboto",sans-serif;color:var(--ink);text-transform:uppercase}
.welcome-text{position:absolute;left:627px;top:775px;width:450px}
.welcome-text p{font:13.5px/26.5px "Roboto",sans-serif;color:var(--text);margin-top:10px}
.welcome-text .h2{margin-top:2px;margin-bottom:8px}
.welcome-text .btn-gold{width:170px;height:47px;margin-top:26px}

/* products */
.products{position:absolute;left:0;top:1245px;width:1200px;height:835px;background:var(--pale)}
.sec-head{position:absolute;left:0;width:1200px;text-align:center}
.card{position:absolute;width:234px;height:292px;background:#fff;overflow:hidden;text-align:center}
.card .pic{position:absolute;left:32px;top:14px;width:170px;height:180px;border-radius:6px}
.card .name{position:absolute;left:0;top:212px;width:100%;font:500 13px "Roboto",sans-serif;text-transform:uppercase;color:#222}
.card .stars{position:absolute;left:0;top:232px;width:100%;color:var(--orange);font-size:13px;letter-spacing:1px}
.card .price{position:absolute;left:0;top:252px;width:100%;font:500 16px "Roboto",sans-serif;color:#111}
.card .price s{color:#777;font-weight:400}
.ribbon{position:absolute;left:-38px;top:26px;width:150px;height:30px;background:var(--orange);color:#fff;transform:rotate(-45deg);font:700 14px "Roboto";display:flex;align-items:center;justify-content:center}

/* news */
.news{position:absolute;width:314px;height:423px;background:#f3f3f3;border-radius:8px;overflow:hidden}
.news .pic{height:209px}
.news .date{position:absolute;left:14px;top:180px;width:58px;height:50px;background:var(--orange);border-radius:6px;color:#fff;text-align:center}
.news .date b{display:block;font:700 26px/30px "Tinos",serif;margin-top:2px}
.news .date small{font:9px "Tinos",serif}
.news h3{position:absolute;left:14px;top:248px;width:290px;font:500 24px/27px "Roboto",sans-serif;color:#111}
.news p{position:absolute;left:14px;top:313px;width:290px;font:14px/25px "Roboto",sans-serif;color:var(--text)}
.news .more{position:absolute;left:14px;top:392px;font:500 14px "Roboto";color:var(--orange)}

/* newsletter */
.newsletter{position:absolute;left:0;top:2790px;width:1200px;height:340px;background:linear-gradient(180deg,#0b52b8,#0a4aa8)}
.newsletter h2{position:absolute;left:0;top:80px;width:1200px;text-align:center;font:700 39px "Roboto";color:#fff}
.newsletter .sub{position:absolute;left:0;top:133px;width:1200px;text-align:center;font:italic 26px "Tinos",serif;color:#fff}
.newsletter .quote{position:absolute;left:0;top:168px;width:1200px;text-align:center;font:15px "Tinos",serif;color:#fff}
.subscribe{position:absolute;left:297px;top:199px;width:606px;height:59px;background:#fff;display:flex;align-items:center;padding:4px}
.subscribe span{flex:1;padding-left:22px;font:16px "Roboto";color:#444}
.subscribe .btn-gold{width:140px;height:51px;text-transform:none;color:#222;font-weight:400}

/* footer */
.footer{position:absolute;left:0;top:3130px;width:1200px;height:360px;background:var(--footer);color:#fff}
.fcol{position:absolute;top:70px}
.fcol h4{font:700 19px "Roboto";text-transform:uppercase;margin-bottom:16px}
.fcol li{list-style:none;font:15px "Roboto";height:33px;color:#eee}
.contact li{display:flex;gap:12px;height:auto;margin-bottom:14px;line-height:22px}
.pay{position:absolute;top:290px;display:flex;gap:14px;left:111px}
.pay i{width:47px;height:30px;background:#fff;border-radius:2px;display:block}
.social{position:absolute;top:292px;left:925px;display:flex;gap:12px}
.social i{width:31px;height:31px;border-radius:50%;background:var(--blue-bright);display:block}
.copy{position:absolute;left:0;top:3490px;width:1200px;height:53px;background:var(--blue-bright);color:#fff;font:15px "Roboto";display:flex;align-items:center;justify-content:center}
</style>
</head>
<body>

<div class="topbar">
  <svg width="16" height="12" viewBox="0 0 16 12"><rect x="0" y="1" width="10" height="8" fill="#fff"/><path d="M10 4h3l3 3v2h-6z" fill="#fff"/><circle cx="3.5" cy="10" r="1.8" fill="#fff"/><circle cx="12.5" cy="10" r="1.8" fill="#fff"/></svg>
  Free Shipping on US Orders over € 30.00
</div>

<header class="header">
  <div class="brand" style="top:38px"><span class="mark"></span>FlintBoro</div>
  <div class="search"><span>search here...</span><div class="btn"><svg width="22" height="22" viewBox="0 0 22 22"><circle cx="12" cy="9" r="6.5" fill="none" stroke="#fff" stroke-width="1.6"/><line x1="7.5" y1="13.5" x2="2" y2="19" stroke="#fff" stroke-width="1.6"/></svg></div></div>
  <div class="call">
    <svg width="36" height="36" viewBox="0 0 36 36"><circle cx="18" cy="18" r="16" fill="none" stroke="var(--orange)" stroke-width="2.5"/><path d="M12 10c-2 2-1 7 4 12s10 6 12 4l-3-4-3 2c-2-1-5-4-6-6l2-3z" fill="var(--orange)"/></svg>
    <div><div class="lbl">Call Us Today</div><div class="num">+31(0)612345678</div></div>
  </div>
  <nav class="nav">
    <a class="active" style="left:294px">HOME</a>
    <a style="left:388px">GLOVES</a>
    <a style="left:495px">MIG</a>
    <a style="left:572px">ABOUT US</a>
    <a style="left:696px">CONTACT US</a>
  </nav>
  <div class="acct" style="left:820px"><svg width="15" height="14" viewBox="0 0 15 14"><rect x="1" y="3" width="10" height="10" fill="none" stroke="var(--blue-bright)" stroke-width="1.5"/><path d="M6 9l7-7" stroke="var(--blue-bright)" stroke-width="2"/></svg>Sign Up <span style="color:#ccc">|</span></div>
  <div class="acct" style="left:913px"><svg width="12" height="14" viewBox="0 0 12 14"><rect x="1" y="6" width="10" height="8" fill="var(--blue-bright)"/><path d="M3 6V4a3 3 0 016 0v2" fill="none" stroke="var(--blue-bright)" stroke-width="1.6"/></svg> Login</div>
  <div class="cart"><span class="badge">0</span><svg width="15" height="13" viewBox="0 0 15 13"><path d="M0 1h3l2 7h8l2-5H4" fill="none" stroke="#222" stroke-width="1.6"/><circle cx="6" cy="11" r="1.5" fill="#222"/><circle cx="12" cy="11" r="1.5" fill="#222"/></svg>Cart</div>
</header>

<section class="hero" role="img" aria-label="Welder in mask and plaid shirt welding metal with bright blue sparks">
  <div class="dots"><i></i><i class="on"></i><i></i><i></i></div>
  <h1>Simple welding of steel &amp; aluminum Get great results with tools that work</h1>
  <div class="btn-gold">Order Now</div>
</section>

<div class="welcome-frame"></div>
<div class="welcome-img" role="img" aria-label="Welder at work surrounded by sparks"></div>
<div class="welcome-text">
  <div class="eyebrow">Welcome To FlintBoro</div>
  <div class="h2">We Deliver Solutions</div>
  <p>Lorem ipsum dolor sit amet, consectetur adipiscing elit, sed do eiusmod tempor incididunt ut labore et dolagna aliqua. Quis ipsum suspendisse ultrices gravida. Risus commodo viverra maecenas accumsan lacus vel facilisis.</p>
  <p style="margin-top:4px">Lorem ipsum dolor sit amet, consectetur adipiscing elit, sed do eiusmod tempor incididunt ut labore et dolagna aliqua. Quis ipsum suspendisse ultrices gravida. Risus commodo</p>
  <div class="btn-gold">Learn More</div>
</div>

<section class="products">
  <div class="sec-head" style="top:63px"><div class="eyebrow">Shop Now</div><div class="h2" style="font-size:37px;margin-top:4px">Our Products</div></div>

  <div class="card" style="left:111px;top:165px"><div class="pic" role="img" aria-label="Red MIG welding machine" style="background:linear-gradient(#d8342f,#8a1b1b)"></div><div class="ribbon">20% OFF</div><div class="name">MIG-250P</div><div class="stars">★★★★★</div><div class="price"><s>€ 845.00</s> € 795.00</div></div>
  <div class="card" style="left:359px;top:165px"><div class="pic" role="img" aria-label="Blue and grey MIG welding machine" style="background:linear-gradient(90deg,#b9bec4,#3a66c8)"></div><div class="name">MIG-2500</div><div class="stars">★★★★★</div><div class="price"><s>€ 845.00</s> € 795.00</div></div>
  <div class="card" style="left:605px;top:165px"><div class="pic" role="img" aria-label="Black welding helmet with purple visor" style="background:radial-gradient(circle at 40% 50%,#8a4fd6 0%,#333 35%,#111 80%)"></div><div class="name">Welding Helmet 180 ..</div><div class="stars">★★★★★</div><div class="price"><s>€ 140.00</s> €109,00</div></div>
  <div class="card" style="left:853px;top:165px"><div class="pic" role="img" aria-label="Blue and yellow welding gloves" style="background:linear-gradient(135deg,#2d3fb8,#e0a43a)"></div><div class="name">Welding Gloves Blue</div><div class="stars">★★★★★</div><div class="price"><s>€ 845.00</s> € 795.00</div></div>

  <div class="card" style="left:111px;top:474px"><div class="pic" role="img" aria-label="Black welding helmet with large view visor" style="background:radial-gradient(circle at 40% 50%,#8a4fd6 0%,#333 35%,#111 80%)"></div><div class="name">Welding Helmet Large View</div><div class="stars">★★★★★</div><div class="price"><s>€ 845.00</s> € 795.00</div></div>
  <div class="card" style="left:359px;top:474px"><div class="pic" role="img" aria-label="Black aluminium speed square, 7 inch" style="background:linear-gradient(135deg,#2b2b2b,#6b5a3e)"></div><div class="name">Kleine Meetdriehoek | 7 Inch</div><div class="stars">★★★★★</div><div class="price"><s>€ 845.00</s> € 795.00</div></div>
  <div class="card" style="left:605px;top:474px"><div class="pic" role="img" aria-label="Black leather welding gloves" style="background:linear-gradient(135deg,#222,#444)"></div><div class="ribbon">20% OFF</div><div class="name">Welding Gloves Black</div><div class="stars">★★★★★</div><div class="price"><s>€ 845.00</s> € 795.00</div></div>
  <div class="card" style="left:853px;top:474px"><div class="pic" role="img" aria-label="Black aluminium speed square, 12 inch" style="background:linear-gradient(135deg,#2b2b2b,#6b5a3e)"></div><div class="name">Grote Meetdriehoek | 12 Inch</div><div class="stars">★★★★★</div><div class="price"><s>€ 845.00</s> € 795.00</div></div>
</section>

<div class="sec-head" style="top:2163px"><div class="eyebrow">Our Latest News</div><div class="h2" style="font-size:37px;margin-top:4px">See What's Trending</div></div>

<article class="news" style="left:111px;top:2264px"><div class="pic" role="img" aria-label="Welder in camouflage welding a steel beam outdoors" style="background:linear-gradient(#9a9488,#5d5a4e)"></div><div class="date"><b>29</b><small>JAN 2021</small></div><h3>The standard Lorem Ipsum passage, used</h3><p>Lorem ipsum dolor sit amet, tur adipiscing elit, sed dood tempor incididunt ut labore et dolore magna aliqua.</p><div class="more">READ MORE »</div></article>
<article class="news" style="left:443px;top:2264px"><div class="pic" role="img" aria-label="Gloved hand holding a welding helmet" style="background:linear-gradient(#6a6e75,#2a2c30)"></div><div class="date"><b>29</b><small>JAN 2021</small></div><h3>The standard Lorem Ipsum passage, used</h3><p>Lorem ipsum dolor sit amet, tur adipiscing elit, sed dood tempor incididunt ut labore et dolore magna aliqua.</p><div class="more">READ MORE »</div></article>
<article class="news" style="left:775px;top:2264px"><div class="pic" role="img" aria-label="Red welding machine with gloves and cables on concrete floor" style="background:linear-gradient(#8c9094,#55595e)"></div><div class="date"><b>29</b><small>JAN 2021</small></div><h3>The standard Lorem Ipsum passage, used</h3><p>Lorem ipsum dolor sit amet, tur adipiscing elit, sed dood tempor incididunt ut labore et dolore magna aliqua.</p><div class="more">READ MORE »</div></article>

<section class="newsletter">
  <h2>SIGN UP TO OUR NEWSLETTER</h2>
  <div class="sub">Receive 10% Off When You Sign Up</div>
  <div class="quote">“Sign up &amp; receive a discount code of 10% off your first order”</div>
  <div class="subscribe"><span>Enter Email Address</span><div class="btn-gold">subscribea</div></div>
</section>

<footer class="footer">
  <div class="fcol" style="left:111px"><h4>Quick Links</h4><ul><li>Home</li><li>Gloves</li><li>Mig</li><li>About us</li><li>Contact us</li></ul></div>
  <div class="fcol" style="left:339px"><h4>Support</h4><ul><li>My Account</li><li>View Cart</li><li>My Wishlist</li><li>Order Status</li><li>Track My Order</li></ul></div>
  <div class="fcol" style="left:552px"><h4>Policies</h4><ul><li>Terms and Conditions</li><li>Privacy Policy</li><li>Shipping &amp; Cancellation Policy</li><li>Assistance Program</li></ul></div>
  <div class="fcol contact" style="left:868px"><h4>Contact Info</h4><ul>
    <li><svg width="16" height="20" viewBox="0 0 16 20"><path d="M8 1a6 6 0 016 6c0 5-6 12-6 12S2 12 2 7a6 6 0 016-6z" fill="none" stroke="var(--blue-bright)" stroke-width="1.8"/><circle cx="8" cy="7" r="2" fill="var(--blue-bright)"/></svg><span>88 Forge Lane Springvale<br>USA 40510</span></li>
    <li><svg width="18" height="14" viewBox="0 0 18 14"><rect x="1" y="1" width="16" height="12" fill="none" stroke="var(--blue-bright)" stroke-width="1.6"/><path d="M1 1l8 7 8-7" fill="none" stroke="var(--blue-bright)" stroke-width="1.6"/></svg><span>+31(0)612345678</span></li>
    <li><svg width="18" height="18" viewBox="0 0 18 18"><path d="M4 2c-2 2-2 6 3 10s8 5 10 3l-3-3-2 2c-2-1-4-3-5-5l2-2z" fill="var(--blue-bright)"/></svg><span>info@flintboro.com</span></li>
  </ul></div>
  <div class="pay"><i></i><i></i><i></i><i></i><i></i></div>
  <div class="social"><i></i><i style="background:#d6246e"></i><i></i><i></i></div>
</footer>
<div class="copy">Copyright © 2021, FlintBoro. All rights</div>

</body>
</html>
```